Improve appearance of one page intro flyer

We modify and upfit medium and heavy duty trucks with equipment needed by the end user. Safety equipment, hydraulic systems, computer systems, etc. We focus on quality and customer service. We have a one page introduction page with wording only. We need graphics or whatever the designer feels would improve the appearance of the flyer and relay professionalism in the presentation.

```html
<!DOCTYPE html>
<html lang="en">
<head>
<meta charset="utf-8">
<title>Ridgeline Custom Trucks – Intro Flyer</title>
<link href="https://fonts.googleapis.com/css2?family=Exo+2:wght@400;500;600;700;800;900&display=swap" rel="stylesheet">
<style>
  :root{
    --navy:#2b2a78;
    --navy-deep:#23225f;
    --lavender:#d9d9fa;
    --panel:#e6e6fd;
    --ink:#1d1d2b;
    --teal:#4aa7bf;
    --teal-light:#8fd0de;
    --white:#ffffff;
    --stage:#d6d6d8;
  }
  *{box-sizing:border-box;margin:0;padding:0}
  html,body{width:1200px;height:940px;overflow:hidden}
  body{background:var(--stage);font-family:"Exo 2",sans-serif;color:var(--ink)}
  .flyer{position:absolute;left:260px;top:20px;width:680px;height:900px;background:var(--lavender);overflow:hidden}
  .hero-photo{position:absolute;left:0;top:0;width:680px;height:400px;
    background:radial-gradient(circle at 80% 58%,#e7a45a 0%,rgba(231,164,90,0) 20%),
               linear-gradient(160deg,var(--teal-light) 0%,var(--teal) 45%,#2f7f95 75%,#3c4a52 100%)}
  .hero-panel{position:absolute;left:0;top:0}
  .brand{position:absolute;left:32px;top:44px;width:420px}
  .brand-mark{display:flex;align-items:center;gap:8px;margin-bottom:4px;margin-left:240px}
  .brand-mark .dot{width:14px;height:14px;border-radius:50%;background:var(--navy)}
  .brand-mark span{font-weight:700;font-size:14px;color:var(--navy)}
  .brand-name{font-weight:900;font-size:58px;line-height:.92;color:var(--navy);letter-spacing:-1px}
  .brand-sub{font-weight:700;font-size:22px;color:var(--navy);letter-spacing:.5px;margin-top:2px}
  .tagline{font-weight:800;font-size:17px;line-height:1.22;color:var(--ink);margin-top:6px}
  h2{font-weight:800;font-size:17px;line-height:1.25;color:var(--navy);text-transform:uppercase;display:flex;align-items:center;gap:8px;letter-spacing:.3px}
  h2 svg{flex:none}
  p{font-size:10.5px;line-height:1.42}
  b{font-weight:800}
  .overview-title{position:absolute;left:32px;top:228px}
  .overview{position:absolute;left:32px;top:268px;width:616px}
  .mission{position:absolute;left:0;top:400px;width:680px;height:100px;background:var(--white);padding:12px 32px}
  .mission p{margin-top:5px}
  .card{position:absolute;background:var(--panel);border-radius:24px;padding:14px 20px;box-shadow:0 8px 18px rgba(43,42,120,.18)}
  .core{left:18px;top:512px;width:360px}
  .core .lead{font-weight:800;font-size:14px;line-height:1.2;margin:6px 0}
  .core p{margin-top:4px}
  .why{left:392px;top:560px;width:272px;padding:14px 18px}
  .why p{margin-top:6px}
  .service-photo{position:absolute;left:0;top:712px;width:680px;height:144px;
    background:linear-gradient(180deg,#e9e9ee 0%,#cfd0d6 100%)}
  .service{position:absolute;left:32px;top:724px;width:350px}
  .service p{margin-top:4px;font-size:10.2px;line-height:1.38}
  .footer{position:absolute;left:0;top:856px;width:680px;height:44px;background:var(--navy-deep);
    display:flex;align-items:center;justify-content:space-around;color:var(--white);font-size:11.5px}
  .footer span{display:flex;align-items:center;gap:6px}
</style>
</head>
<body>
<main class="flyer">
  <div class="hero-photo" role="img" aria-label="Red heavy-duty truck on a highway under a teal sky with snowfall"></div>

  <svg class="hero-panel" width="680" height="400" viewBox="0 0 680 400" aria-hidden="true">
    <path d="M0 90 L360 30 Q408 22 420 66 L456 236 Q462 262 434 262 L0 262 Z" fill="var(--panel)"/>
    <path d="M0 262 L434 262 Q462 262 456 236" fill="none" stroke="var(--navy)" stroke-width="4"/>
    <rect x="0" y="262" width="680" height="138" fill="var(--lavender)"/>
  </svg>

  <header class="brand">
    <div class="brand-mark"><i class="dot"></i><span>Ridgeline</span></div>
    <h1 class="brand-name">RIDGELINE</h1>
    <div class="brand-sub">CUSTOM TRUCKS, INC.</div>
    <div class="tagline">Excellence in Custom Truck<br>Modification and Upfitting</div>
  </header>

  <h2 class="overview-title"><svg width="16" height="16" viewBox="0 0 18 18"><rect x="2" y="2" width="12" height="14" rx="2" fill="none" stroke="var(--navy)" stroke-width="1.6"/><circle cx="12" cy="12" r="3" fill="none" stroke="var(--navy)" stroke-width="1.6"/></svg>Overview</h2>
  <section class="overview">
    <p>Having more than 30 years in the truck modification industry, Ridgeline Custom Trucks, Inc. specializes in medium- and heavy-duty truck modification and custom-designed upfitting. Based in North Carolina, we transform standard commercial trucks into purpose-built machines designed to meet each customer's specific needs. From component integration to specialized equipment installations, our specialists provide engineered solutions for all vehicle modifications. At Ridgeline Custom Trucks we're redefining what truck performance and customization can be. Our foundation lies in precision product engineering and quality craftsmanship, ensuring every facet, from upgrades to custom fabrication, is built to last and perform flawlessly. Driven by constant research and development, our team's design experts are always exploring new technologies, materials, and design improvements to push the limits of what's possible.</p>
  </section>

  <section class="mission">
    <h2><svg width="16" height="16" viewBox="0 0 18 18"><path d="M4 16 V2 L14 5 L4 8" fill="none" stroke="var(--navy)" stroke-width="1.6"/><path d="M1 16 H17" stroke="var(--navy)" stroke-width="1.6"/></svg>Mission Statement</h2>
    <p>Our mission is to redefine quality in truck modification and upfitting by combining craftsmanship, innovation, and reliability. At Ridgeline Custom Trucks, our team excels in the highest quality workmanship and reflects the pride and professionalism in everything we do.</p>
  </section>

  <div class="service-photo" role="img" aria-label="Faded greyscale row of trucks parked at a service yard"></div>

  <section class="card core">
    <h2><svg width="16" height="16" viewBox="0 0 18 18"><circle cx="9" cy="9" r="3" fill="none" stroke="var(--navy)" stroke-width="1.6"/><circle cx="9" cy="9" r="7" fill="none" stroke="var(--navy)" stroke-width="1.6" stroke-dasharray="3 2"/></svg>Core Services</h2>
    <div class="lead">Excellent customer service is the core of our business.</div>
    <p><b>Custom Truck Upfitting:</b> Tailored designs for vocational and fleet applications — customer-specified safety equipment, computer and camera systems, fenders, decals, tool systems, lighting, hydraulic integration, and much more…</p>
    <p><b>Specialized Solutions:</b> Customer interaction to identify and offer specialized solutions to increase efficiency, safety, and reliability.</p>
  </section>

  <section class="card why">
    <h2><svg width="16" height="16" viewBox="0 0 18 18"><path d="M3 9 L7 13 L15 4" fill="none" stroke="var(--navy)" stroke-width="2"/></svg>Why Choose Ridgeline Custom Trucks</h2>
    <p>Our team brings more than 100 years of hands-on expertise in fabrication, mechanical design, and truck engineering. Every project reflects our core commitment to Excellence in Every Detail — precision craftsmanship, reliable performance, and tailored functionality that meets each customer's unique operational goals. Our product engineering, design, and quality is what sets us apart as leaders in the truck industry.</p>
  </section>

  <section class="service">
    <h2><svg width="16" height="16" viewBox="0 0 18 18"><circle cx="9" cy="9" r="7" fill="none" stroke="var(--navy)" stroke-width="1.6"/><path d="M2 9 H16 M9 2 Q13 9 9 16 Q5 9 9 2" fill="none" stroke="var(--navy)" stroke-width="1.2"/></svg>Service Area</h2>
    <p>Serving customers internationally, Ridgeline Custom Trucks, Inc. provides end-to-end solutions for all the major truck manufacturers — from concept and design through final delivery — with nationwide logistics coordination. We are honored to be part of Halvorsen's Ship Thru service, providing complete upfit service to your new Halvorsen truck — in most cases without any additional shipping charges — delivered directly to your location.</p>
  </section>

  <footer class="footer">
    <span><svg width="12" height="14" viewBox="0 0 12 14"><path d="M6 13 C2 8 1 6 1 5 A5 5 0 0 1 11 5 C11 6 10 8 6 13Z" fill="var(--white)"/><circle cx="6" cy="5" r="1.8" fill="var(--navy-deep)"/></svg>410 Meridian Works Drive - Charlotte, NC - 28206</span>
    <span><svg width="13" height="13" viewBox="0 0 13 13"><path d="M3 1 L5 4 L4 5.5 Q5.5 8 7.5 9 L9 8 L12 10 L10.5 12 Q5 12 1 5 Q1 2.5 3 1Z" fill="var(--white)"/></svg>555-014-2270</span>
    <span><svg width="14" height="11" viewBox="0 0 14 11"><rect x="0.5" y="0.5" width="13" height="10" rx="1" fill="var(--white)"/><path d="M1 1 L7 6 L13 1" fill="none" stroke="var(--navy-deep)" stroke-width="1.2"/></svg>info@ridgelinecustomtrucks.com</span>
  </footer>
</main>
</body>
</html>
```